Designer Instructions – Updated Referral Program Flyer

(Based on the mock-up in “Brief Layout and Instructions.pdf”)

OVERALL STYLE + LAYOUT

Maintain the same general layout, structure, and flow as the mock-up flyer (front and back).

This is an update of an older flyer, not a full redesign — keep the same sections, proportions, and overall visual feel, but with cleaner, more modern design improvements.

The final flyer should look clean, bold, professional, and high-impact, geared toward realtors, property managers, and contractors who refer work.

FRONT SIDE INSTRUCTIONS
1. Header Section

Remove the Rebuild Harbor Crest logo from the top banner.
(Shown on page 1 of the PDF)

2. Main Headline

Keep the same three-line structure:
EARN
UNLIMITED
CASH

Center it, maximize impact, and increase the font size of CASH so all three words match in importance.

Make the headline bold, clean, and the main focal point.

3. Cash Incentive Box

Keep the "$500 minimum OR 10% per referral" box, but upgrade the graphics to look sharper and more modern.

Ensure the wording matches exactly what’s in the mock-up.

4. Premier Partner Program Ribbon

Clean up and modernize the "PREMIER PARTNER PROGRAM" bar while keeping the same position and structure.

Ensure the checkmark badge remains crisp and professional.

5. Supporting Icons Section

Keep the four icons/benefit boxes (Guaranteed Payout, Free Evaluations, Affordable Solutions, Industry Leaders) in the same order.

Update the icons to cleaner, more modern styles — but maintain the same meanings.

Improve alignment and spacing for sharper visual consistency.

6. Remove Icons in Contact Area

At the bottom (“CALL TEXT OR BOOK ONLINE 858-471-6093 BrightlaneRenovate.com”), remove the phone and internet icons, as noted on page 2 of the PDF.

7. Replace All Images

I (Dorian) will provide all updated stock images separately via email.

Replace the flood/water-damage imagery and roof leak with the new images I send.

Keep image placement and proportions the same as the mock-up.

BACK SIDE INSTRUCTIONS
1. Header Image + “REFER / EARN” Section

Maintain the same large split-image layout (“The more you refer, the more you earn”).

Replace all background imagery with the new assets I will send.

Keep the CASH FLOW image section but modernize the type and spacing.

2. “HOW IT WORKS” Section

Preserve the three-column layout:

Refer Flood, Water & Mold Damage

We Take Care of Everything (evaluations/insurance)

Get Paid to Share

Update images, tighten spacing, and use modern iconography.

3. Remove Phone/Internet Icons

Same as the front side — remove small communication icons and keep only the text/number/URL.

4. Bottom Contact Bar

Keep the blue bar, same wording, same layout — just modernize the style if needed for clarity.

5. Replace All Back-Side Images

Again, I will email you the image assets.

Keep the layout EXACT — just update with higher-quality photos and improved design.

TEXT CONTENT (Keep as-is unless spacing adjustments needed)

All text shown in the PDF should remain exactly the same unless spacing or visual balance requires minor adjustments.
Example from page 3:

“REFER FLOOD, MOLD & CONSTRUCTION JOBS”

“We Schedule a Free Estimate. If Approved, You Get Paid.”

“Everybody Benefits From Referrals”

Everything stays, just refreshed and visually improved.

DESIGN GOALS

Flyer should look high-end and trustworthy, not salesy.

Consistent color theme: blues, whites, yellows, same palette as original.

Use bold, modern fonts with strong readability.

Ensure all headlines pop and all benefit boxes are clean, well-aligned, and evenly spaced.

The final result should feel like a premium referral program flyer for a top-tier restoration/remodel company.

FILES I WILL PROVIDE

I will send the designer:

All replacement stock photos

Any updated logos (if needed)

Original high-resolution version of the mock-up (if available)

Any additional icons preferred

Colors
0054AA
0677BA
7BADD7
CADEEF
E8F1F8

Requirements
Must have
• Designer Instructions – Updated Referral Program Flyer (Based on the mock-up in “Brief Layout and Instructions.pdf”) OVERALL STYLE + LAYOUT Maintain the same general layout, structure, and flow as the mock-up flyer (front and back). This is an update of an older flyer, not a full redesign — keep the same sections, proportions, and overall visual feel, but with cleaner, more modern design improvements. The final flyer should look clean, bold, professional, and high-impact, geared toward realtors, property managers, and contractors who refer work. FRONT SIDE INSTRUCTIONS 1. Header Section Remove the Rebuild Harbor Crest logo from the top banner. (Shown on page 1 of the PDF) 2. Main Headline Keep the same three-line structure: EARN UNLIMITED CASH Center it, maximize impact, and increase the font size of CASH so all three words match in importance. Make the headline bold, clean, and the main focal point. 3. Cash Incentive Box Keep the "$500 minimum OR 10% per referral" box, but upgrade the graphics to look sharper and more modern. Ensure the wording matches exactly what’s in the mock-up. 4. Premier Partner Program Ribbon Clean up and modernize the "PREMIER PARTNER PROGRAM" bar while keeping the same position and structure. Ensure the checkmark badge remains crisp and professional. 5. Supporting Icons Section Keep the four icons/benefit boxes (Guaranteed Payout, Free Evaluations, Affordable Solutions, Industry Leaders) in the same order. Update the icons to cleaner, more modern styles — but maintain the same meanings. Improve alignment and spacing for sharper visual consistency. 6. Remove Icons in Contact Area At the bottom (“CALL TEXT OR BOOK ONLINE 858-471-6093 BrightlaneRenovate.com”), remove the phone and internet icons, as noted on page 2 of the PDF. 7. Replace All Images I (Dorian) will provide all updated stock images separately via email. Replace the flood/water-damage imagery and roof leak with the new images I send. Keep image placement and proportions the same as the mock-up. BACK SIDE INSTRUCTIONS 1. Header Image + “REFER / EARN” Section Maintain the same large split-image layout (“The more you refer, the more you earn”). Replace all background imagery with the new assets I will send. Keep the CASH FLOW image section but modernize the type and spacing. 2. “HOW IT WORKS” Section Preserve the three-column layout: Refer Flood, Water & Mold Damage We Take Care of Everything (evaluations/insurance) Get Paid to Share Update images, tighten spacing, and use modern iconography. 3. Remove Phone/Internet Icons Same as the front side — remove small communication icons and keep only the text/number/URL. 4. Bottom Contact Bar Keep the blue bar, same wording, same layout — just modernize the style if needed for clarity. 5. Replace All Back-Side Images Again, I will email you the image assets. Keep the layout EXACT — just update with higher-quality photos and improved design. TEXT CONTENT (Keep as-is unless spacing adjustments needed) All text shown in the PDF should remain exactly the same unless spacing or visual balance requires minor adjustments. Example from page 3: “REFER FLOOD, MOLD & CONSTRUCTION JOBS” “We Schedule a Free Estimate. If Approved, You Get Paid.” “Everybody Benefits From Referrals” Everything stays, just refreshed and visually improved. DESIGN GOALS Flyer should look high-end and trustworthy, not salesy. Consistent color theme: blues, whites, yellows, same palette as original. Use bold, modern fonts with strong readability. Ensure all headlines pop and all benefit boxes are clean, well-aligned, and evenly spaced. The final result should feel like a premium referral program flyer for a top-tier restoration/remodel company. FILES I WILL PROVIDE I will send the designer: All replacement stock photos Any updated logos (if needed) Original high-resolution version of the mock-up (if available) Any additional icons preferred

```html
<!DOCTYPE html>
<html lang="en">
<head>
<meta charset="utf-8">
<title>Earn Unlimited Cash – Referral Partner Flyer</title>
<link rel="stylesheet" href="https://fonts.googleapis.com/css2?family=Montserrat:wght@500;600;700;800;900&display=swap">
<style>
  :root{
    --navy:#0a1c9e;
    --navy-deep:#071783;
    --sky:#1f6fe6;
    --sky-light:#4f97f4;
    --sky-pale:#9cc6ff;
    --yellow:#f7ec0a;
    --red:#e10f12;
    --white:#ffffff;
    --silver:#c9ccd2;
    --card-top:#f4f5f7;
    --card-bottom:#c9ced6;
    --ink-blue:#0a1aa0;
  }
  *{box-sizing:border-box;margin:0;padding:0}
  html,body{width:1200px;height:800px;overflow:hidden;background:#fff}
  body{font-family:"Montserrat",Arial,sans-serif}
  .flyer{position:relative;width:1200px;height:800px;overflow:hidden;background:var(--sky)}

  /* ---------- top hero ---------- */
  .hero{position:absolute;left:0;top:0;width:1200px;height:385px;background:var(--navy)}
  .hero-art{position:absolute;left:0;top:0}
  .license-line{position:absolute;left:0;width:640px;top:44px;text-align:center;color:var(--white);font-weight:500;font-size:15px;letter-spacing:-.1px}
  .headline{position:absolute;left:0;width:640px;top:56px;text-align:center;font-weight:900;line-height:1;letter-spacing:-3px}
  .headline-earn{display:block;color:var(--yellow);font-size:124px;line-height:106px}
  .headline-unlimited{display:block;color:var(--white);font-size:55px;line-height:52px;letter-spacing:-1px;margin-top:6px}
  .headline-cash{display:block;color:var(--white);font-size:128px;line-height:104px;margin-top:-2px}
  .tagline-band{position:absolute;left:0;top:322px;width:690px;height:44px;background:var(--yellow);clip-path:polygon(0 0,668px 0,690px 44px,0 44px)}
  .tagline{position:absolute;left:0;width:690px;top:326px;text-align:center;padding-right:70px;color:var(--navy);font-weight:800;font-size:29px;letter-spacing:-.3px}

  .emergency-badge{position:absolute;left:975px;top:0;width:146px;height:176px}
  .badge-text{position:absolute;left:975px;top:0;width:146px;text-align:center;color:var(--white);font-weight:900}
  .badge-number{display:block;font-size:54px;line-height:54px;margin-top:52px;letter-spacing:-3px}
  .badge-hour{display:block;font-size:16px;line-height:18px}
  .badge-service{display:block;font-size:10px;line-height:12px;letter-spacing:.4px}

  /* ---------- lower panel ---------- */
  .lower{position:absolute;left:0;top:385px;width:1200px;height:415px;
    background:radial-gradient(circle at 30% 40%,var(--sky-light),transparent 55%),
               radial-gradient(circle at 80% 70%,#3a86f0,transparent 50%),
               linear-gradient(180deg,#2a78ea,#1a63da)}

  .incentive{position:absolute;left:81px;top:402px;width:563px;height:92px;background:var(--red);border-radius:14px;box-shadow:0 3px 6px rgba(0,0,0,.25)}
  .incentive-min{position:absolute;left:22px;top:6px;width:130px;text-align:center;color:var(--white);font-weight:900}
  .incentive-amount{display:block;font-size:50px;line-height:52px;letter-spacing:-1px}
  .incentive-label{display:block;font-size:22px;line-height:24px}
  .incentive-or{position:absolute;left:158px;top:-2px;width:92px;height:92px;border-radius:50%;background:var(--white);color:var(--navy);font-weight:900;font-size:33px;display:flex;align-items:center;justify-content:center}
  .incentive-pct{position:absolute;left:270px;top:10px;color:var(--white);font-weight:900;font-size:64px;line-height:66px;letter-spacing:-2px}
  .incentive-note{position:absolute;left:420px;top:24px;color:var(--white);font-weight:800;font-size:22px;line-height:21px;letter-spacing:.5px}

  .partner-ribbon{position:absolute;left:656px;top:402px;width:455px;height:92px}
  .ribbon-cap{position:absolute;left:0;top:0;width:455px;height:30px;border-radius:12px 12px 0 0;background:linear-gradient(180deg,#e1e3e6,#b8bcc3);color:var(--red);font-weight:600;font-size:22px;letter-spacing:27px;text-align:center;line-height:30px;padding-left:27px}
  .ribbon-left{position:absolute;left:0;top:30px;width:230px;height:62px;background:var(--red);border-radius:0 0 0 12px}
  .ribbon-right{position:absolute;left:230px;top:30px;width:225px;height:62px;background:var(--navy);border-radius:0 0 12px 0}
  .ribbon-word{position:absolute;top:40px;color:var(--white);font-weight:900;font-size:31px;letter-spacing:2px}
  .ribbon-word.partner{left:20px}
  .ribbon-word.program{left:268px}
  .ribbon-shield{position:absolute;left:198px;top:28px}

  .wins{position:absolute;left:0;width:1200px;top:500px;text-align:center;color:var(--white);font-weight:900;font-size:40px;letter-spacing:3.4px;text-shadow:0 2px 3px rgba(0,0,40,.35)}

  .benefits{position:absolute;left:96px;top:552px;width:1012px;display:flex;justify-content:space-between}
  .benefit{width:228px;height:108px;border:2px solid var(--navy-deep);border-radius:10px;overflow:hidden;background:linear-gradient(180deg,var(--card-top),var(--card-bottom));position:relative;box-shadow:0 2px 5px rgba(0,0,40,.3)}
  .benefit-title{height:48px;background:var(--navy);color:var(--white);font-weight:800;font-size:17px;line-height:18px;text-align:center;padding-top:7px;letter-spacing:.3px;border-radius:0 0 8px 8px}
  .benefit-text{position:absolute;left:18px;top:55px;width:152px;color:var(--ink-blue);font-weight:700;font-size:12px;line-height:15px}
  .benefit-icon{position:absolute;right:8px;top:54px}

  .slogan{position:absolute;left:0;width:1200px;top:667px;text-align:center;font-weight:900;font-size:33px;letter-spacing:.6px;color:var(--white);text-shadow:0 2px 3px rgba(0,0,40,.35)}
  .slogan .hi{color:var(--yellow)}

  .contact-bar{position:absolute;left:0;top:725px;width:477px;height:75px;background:var(--navy-deep);clip-path:polygon(0 0,420px 0,477px 75px,0 75px)}
  .contact-cta{position:absolute;left:96px;top:740px;color:var(--white);font-size:34px;letter-spacing:2px;font-weight:900}
  .contact-cta .thin{font-weight:500}
  .contact-details{position:absolute;left:482px;top:738px;color:var(--white);font-weight:700;font-size:35px;letter-spacing:1px}
</style>
</head>
<body>
<main class="flyer">

  <section class="hero">
    <svg class="hero-art" width="1200" height="385" viewBox="0 0 1200 385">
      <defs>
        <linearGradient id="kitchenTone" x1="0" y1="0" x2="0" y2="1">
          <stop offset="0" stop-color="#dfe6ec"/>
          <stop offset=".45" stop-color="#c5d3de"/>
          <stop offset=".7" stop-color="#8fa7bb"/>
          <stop offset="1" stop-color="#3d4347"/>
        </linearGradient>
        <linearGradient id="silverEdge" x1="0" y1="0" x2="1" y2="1">
          <stop offset="0" stop-color="#eef0f3"/>
          <stop offset="1" stop-color="#8c9199"/>
        </linearGradient>
      </defs>
      <polygon points="648,0 670,0 618,178 706,385 680,385 594,178" fill="url(#silverEdge)"/>
      <polygon points="670,0 1200,0 1200,385 706,385 618,178" fill="url(#kitchenTone)" role="img" aria-label="Photo of a bright white kitchen with water pouring from the ceiling onto a flooded floor"/>
    </svg>

    <p class="license-line">Tidewater Cleaning &amp; Restoration Inc. CSLB Lic. #2048913</p>
    <h1 class="headline">
      <span class="headline-earn">EARN</span>
      <span class="headline-unlimited">UNLIMITED</span>
      <span class="headline-cash">CASH</span>
    </h1>
    <div class="tagline-band"></div>
    <p class="tagline">GET PAID TO REFER A FLOOD</p>

    <svg class="emergency-badge" width="146" height="176" viewBox="0 0 146 176">
      <rect x="0" y="0" width="146" height="120" fill="var(--white)"/>
      <rect x="0" y="0" width="2" height="120" fill="var(--red)"/>
      <rect x="144" y="0" width="2" height="120" fill="var(--red)"/>
      <circle cx="73" cy="102" r="70" fill="var(--white)"/>
      <circle cx="73" cy="102" r="65" fill="var(--red)"/>
    </svg>
    <div class="badge-text">
      <span class="badge-number">24</span>
      <span class="badge-hour">HOUR</span>
      <span class="badge-service">EMERGENCY<br>SERVICE</span>
    </div>
  </section>

  <section class="lower"></section>

  <div class="incentive">
    <div class="incentive-min">
      <span class="incentive-amount">$500</span>
      <span class="incentive-label">MINIMUM</span>
    </div>
    <div class="incentive-or">OR</div>
    <div class="incentive-pct">10%</div>
    <div class="incentive-note">OF TOTAL<br>INVOICE</div>
  </div>

  <div class="partner-ribbon">
    <div class="ribbon-cap">PREMIER</div>
    <div class="ribbon-left"></div>
    <div class="ribbon-right"></div>
    <span class="ribbon-word partner">PARTNER</span>
    <span class="ribbon-word program">PROGRAM</span>
    <svg class="ribbon-shield" width="60" height="68" viewBox="0 0 60 68">
      <path d="M30 2 L57 10 V34 C57 50 45 61 30 66 C15 61 3 50 3 34 V10 Z" fill="#d7dade" stroke="#9aa0a8" stroke-width="2"/>
      <path d="M30 8 L51 14 V34 C51 47 42 55 30 60 C18 55 9 47 9 34 V14 Z" fill="var(--white)"/>
      <path d="M17 33 L27 43 L44 24" fill="none" stroke="var(--red)" stroke-width="7" stroke-linecap="round" stroke-linejoin="round"/>
    </svg>
  </div>

  <h2 class="wins">PARTNER WITH US &amp; EVERYBODY WINS!</h2>

  <div class="benefits">
    <article class="benefit">
      <h3 class="benefit-title">EVERYONE<br>CAN REFER</h3>
      <p class="benefit-text">Plumbers, Contractors, Agents, Roofers &amp; Friends</p>
      <svg class="benefit-icon" width="46" height="46" viewBox="0 0 48 48">
        <circle cx="24" cy="24" r="21" fill="none" stroke="var(--red)" stroke-width="3" stroke-dasharray="6 2"/>
        <circle cx="24" cy="24" r="15" fill="none" stroke="var(--red)" stroke-width="3"/>
        <path d="M17 24 L22 29 L31 19" fill="none" stroke="var(--red)" stroke-width="3.5" stroke-linecap="round" stroke-linejoin="round"/>
      </svg>
    </article>
    <article class="benefit">
      <h3 class="benefit-title">INSURANCE<br>SPECIALISTS</h3>
      <p class="benefit-text">We Use ClaimScope To Secure Clients The Maximum Payout</p>
      <svg class="benefit-icon" width="42" height="48" viewBox="0 0 44 50">
        <rect x="4" y="4" width="28" height="40" rx="3" fill="none" stroke="var(--red)" stroke-width="3"/>
        <rect x="12" y="1" width="12" height="6" rx="2" fill="var(--red)"/>
        <path d="M10 15 H26 M10 22 H26 M10 29 H22" stroke="var(--red)" stroke-width="2.5"/>
        <circle cx="33" cy="38" r="9" fill="var(--white)" stroke="var(--red)" stroke-width="3"/>
        <text x="33" y="43" text-anchor="middle" font-family="Montserrat, sans-serif" font-weight="800" font-size="13" fill="var(--red)">$</text>
      </svg>
    </article>
    <article class="benefit">
      <h3 class="benefit-title">AFFORDABLE<br>SOLUTIONS</h3>
      <p class="benefit-text">We Offer Lowest Out of Pocket Costs for Your Customers</p>
      <svg class="benefit-icon" width="46" height="46" viewBox="0 0 50 50">
        <path d="M4 10 C14 4 28 4 46 6 L44 14 C32 12 20 12 8 14 Z" fill="none" stroke="var(--red)" stroke-width="3" stroke-linejoin="round"/>
        <circle cx="25" cy="26" r="9" fill="none" stroke="var(--red)" stroke-width="3"/>
        <text x="25" y="31" text-anchor="middle" font-family="Montserrat, sans-serif" font-weight="800" font-size="13" fill="var(--red)">$</text>
        <path d="M4 40 C16 36 30 36 44 38 L42 46 C30 44 18 44 6 46 Z" fill="none" stroke="var(--red)" stroke-width="3" stroke-linejoin="round"/>
      </svg>
    </article>
    <article class="benefit">
      <h3 class="benefit-title">INDUSTRY<br>LEADERS</h3>
      <p class="benefit-text">We are ARSC Certified Licensed General Contractors</p>
      <svg class="benefit-icon" width="42" height="46" viewBox="0 0 46 50">
        <circle cx="23" cy="17" r="13" fill="none" stroke="var(--red)" stroke-width="3"/>
        <path d="M23 9 L25.5 14.5 L31 15 L27 19 L28 25 L23 22 L18 25 L19 19 L15 15 L20.5 14.5 Z" fill="var(--red)"/>
        <path d="M14 28 L9 46 L16 42 L19 48 L23 31 M32 28 L37 46 L30 42 L27 48 L23 31" fill="none" stroke="var(--red)" stroke-width="3" stroke-linejoin="round"/>
      </svg>
    </article>
  </div>

  <p class="slogan">SEND <span class="hi">REFERRALS.</span> GET <span class="hi">PAID.</span> GROW <span class="hi">YOUR BUSINESS.</span></p>

  <div class="contact-bar"></div>
  <p class="contact-cta">CALL <span class="thin">OR</span> TEXT</p>
  <p class="contact-details">858·471·6093 • BayTideRestore.com</p>

</main>
</body>
</html>
```